TK Stationery - Modern Contemporary

Develop modern template for Letterhead and Stationery (business card, letterhead, envelopes) using the TK Logo and Icon

Colors
0054AA
0677BA
7BADD7
CADEEF
E8F1F8
00AB8E
00BBA5
67D7C9
C6EFE9
E9F9F6
EE7325
F08F49
F5BC92
FAE3D3
FDF4ED
6B429C
8869AF
B7A5CE
E3DAEB
F3F0F8

```html
<!DOCTYPE html>
<html lang="en">
<head>
<meta charset="utf-8">
<title>Terra Kova Stationery</title>
<link rel="stylesheet" href="https://fonts.googleapis.com/css2?family=DM+Serif+Display&family=Arimo:wght@400;700&display=swap">
<style>
:root{
  --stage:#a9a8a9;
  --paper:#fafafa;
  --green:#36b677;
  --green-bright:#1fc174;
  --green-deep:#2ea46b;
  --navy:#2a2f45;
  --orange:#f07f2a;
  --ink:#3a3a3a;
  --grey-text:#555;
}
*{box-sizing:border-box;margin:0;padding:0}
html,body{width:828px;height:1200px;overflow:hidden}
body{background:var(--stage);position:relative;font-family:"Arimo",Arial,sans-serif;color:var(--ink)}
.piece{position:absolute;box-shadow:1px 2px 3px rgba(0,0,0,.28);overflow:hidden}
.wordmark{font-family:"DM Serif Display",Georgia,serif;font-weight:400;color:var(--navy);white-space:nowrap;letter-spacing:.4px;line-height:1}
.footer{position:absolute;left:0;bottom:0}
.footer svg{display:block}
.footer .web{position:absolute;left:0;top:0;color:#fff;font-weight:700;white-space:nowrap}

/* business card front */
.card-front{left:57px;top:58px;width:305px;height:174px;background:var(--paper)}
.card-front .wordmark{position:absolute;right:17px;top:20px;font-size:24px}
.card-front .holder-name{position:absolute;left:17px;top:92px;font-size:10.5px;font-weight:700;color:var(--green)}
.card-front .holder-role{position:absolute;left:17px;top:105px;font-size:8.3px;color:var(--ink)}
.card-front .rule{position:absolute;left:17px;top:118px;width:271px;height:1px;background:var(--green)}
.contact-list{position:absolute;list-style:none}
.contact-list li{display:flex;align-items:center;gap:4px;white-space:nowrap}
.card-front .contact-list{left:17px;top:126px;font-size:8.2px;line-height:11px}
.card-front .address{position:absolute;right:17px;top:126px;font-size:8.2px;line-height:11px;text-align:right}
.card-front .footer .web{font-size:7.6px;left:19px;top:3px}

/* letterhead strip / DL envelope front */
.envelope-front{left:390px;top:66px;width:395px;height:172px;background:var(--paper)}
.envelope-front .wordmark{position:absolute;left:13px;top:12px;font-size:12px}
.envelope-front .address{position:absolute;left:13px;top:25px;font-size:4.4px;line-height:5px}
.envelope-front .footer .web{font-size:7.4px;left:13px;top:3px}

/* card backs */
.card-back{left:57px;top:254px;width:305px;height:174px;background:var(--green);display:flex;align-items:center;justify-content:center}
.card-back .wordmark{font-size:28px;margin-top:-6px}
.card-emboss{left:57px;top:457px;width:305px;height:174px;background:var(--green);display:flex;align-items:center;justify-content:center}
.card-emboss .wordmark{font-size:28px;color:var(--green-deep);margin-top:-6px}

/* envelope backs */
.envelope-back{left:390px;width:395px;height:172px;background:var(--paper)}
.envelope-back.white-flap{top:262px}
.envelope-back.green-flap{top:459px;background:#fff}
.envelope-back .flap{position:absolute;left:0;top:0;filter:drop-shadow(0 3px 3px rgba(0,0,0,.18))}
.envelope-back .wordmark{position:absolute;left:0;right:0;top:14px;text-align:center;font-size:17px}
.envelope-back.green-flap .wordmark{color:#fff}

/* letter */
.letter{left:51px;top:660px;width:359px;height:509px;background:var(--paper)}
.letter-head{position:absolute;left:31px;top:26px;width:296px;height:26px;border-bottom:1px solid var(--green);display:flex;align-items:flex-start}
.letter-head .wordmark{font-size:20px;margin-top:0}
.letter-head .divider{width:1px;height:15px;background:var(--green);margin:3px 14px 0}
.letter-head .contact-list{position:static;font-size:5.8px;line-height:7.3px;margin-top:3px}
.letter-head .address{font-size:5.8px;line-height:7.3px;margin-top:3px;white-space:nowrap}
.letter-body{position:absolute;left:31px;top:157px;width:296px}
.salutation{font-size:8px;font-weight:700;color:#444;margin-bottom:12px}
.letter-body p{font-size:5.7px;line-height:7.4px;color:#555;margin-bottom:6px;text-align:justify}
.closing{font-size:4.8px;font-weight:700;color:#444;margin-top:10px}
.signature{width:60px;height:14px;margin-top:9px;background:linear-gradient(90deg,rgba(42,47,69,.35),rgba(42,47,69,.12))}
.letter .footer .web{font-size:7.6px;left:32px;top:3px}

/* folders */
.folder-closed{left:436px;top:660px;width:341px;height:241px;background:#fff}
.folder-cover{position:absolute;left:0;top:0;width:170px;height:241px;background:var(--green-bright);display:flex;align-items:center;justify-content:center}
.folder-cover .wordmark{font-size:16px;margin-top:-6px}
.folder-inside{position:absolute;left:170px;top:0;width:171px;height:241px;background:linear-gradient(90deg,#e4e4e4,#fafafa 45%,#fff)}
.mini-head{position:absolute;display:flex;align-items:flex-start;border-bottom:.6px solid var(--green)}
.mini-head .wordmark{font-size:8.5px}
.mini-head .divider{width:.5px;height:7px;background:var(--green);margin:1px 6px 0}
.mini-head .mini-text{font-size:2.4px;line-height:3px;white-space:nowrap;margin-top:1px}
.folder-inside .mini-head{left:15px;top:10px;width:140px;height:13px}
.folder-inside .footer .web{font-size:3px;left:15px;top:1px}

.folder-open{left:436px;top:927px;width:341px;height:241px;background:#fff}
.folder-open .left-panel{position:absolute;left:0;top:0;width:170px;height:241px;background:linear-gradient(90deg,#fff 10%,#e2e2e2)}
.folder-open .fold-gap{position:absolute;left:170px;top:0;width:8px;height:241px;background:#d9d9d9}
.mini-letter{position:absolute;left:178px;top:8px;width:153px;height:170px;background:var(--paper);box-shadow:0 0 2px rgba(0,0,0,.2)}
.mini-letter .mini-head{left:13px;top:12px;width:127px;height:12px}
.mini-letter .mini-head .wordmark{font-size:8px}
.mini-body{position:absolute;left:13px;top:66px;width:127px}
.mini-body .salutation{font-size:3.2px;margin-bottom:5px}
.mini-body p{font-size:2.3px;line-height:3px;color:#666;margin-bottom:2.5px;text-align:justify}
.mini-body .closing{font-size:2.2px;margin-top:3px}
.pockets{position:absolute;left:0;top:0}
</style>
</head>
<body>

<!-- business card front -->
<section class="piece card-front" aria-label="Business card front">
  <div class="wordmark">terra kova</div>
  <h2 class="holder-name">DANIEL REYES</h2>
  <p class="holder-role">Manager</p>
  <div class="rule"></div>
  <ul class="contact-list">
    <li><svg width="7" height="7" viewBox="0 0 10 10"><path d="M2 1l2 2-1 1.4c.6 1.2 1.4 2 2.6 2.6L7 6l2 2-1.4 1.5C4.5 9 1 5.5.5 2.4z" fill="#36b677"/></svg>555-014-2100</li>
    <li><svg width="7" height="7" viewBox="0 0 10 10"><rect x=".8" y="2" width="8.4" height="6" fill="none" stroke="#36b677" stroke-width="1"/><path d="M1 2.3l4 3 4-3" fill="none" stroke="#36b677" stroke-width="1"/></svg>info@terrakova.com</li>
  </ul>
  <p class="address">Your address, city<br>state, ZIP 0000</p>
  <div class="footer">
    <svg width="305" height="16" viewBox="0 0 305 16">
      <path d="M0 0H128Q133 0 137 5L141 11H305V16H0Z" fill="#36b677"/>
      <rect x="138" y="6.5" width="85" height="2.3" fill="#f07f2a"/>
      <rect x="226" y="6.5" width="79" height="2.3" fill="#2a2f45"/>
    </svg>
    <span class="web">www.terrakova.com</span>
  </div>
</section>

<!-- envelope front -->
<section class="piece envelope-front" aria-label="Envelope front">
  <div class="wordmark">terra kova</div>
  <p class="address">Your address, city<br>state, ZIP 0000</p>
  <div class="footer">
    <svg width="395" height="17" viewBox="0 0 395 17">
      <path d="M0 0H120Q125 0 129 5L134 12H395V17H0Z" fill="#36b677"/>
      <rect x="131" y="7" width="136" height="2.4" fill="#f07f2a"/>
      <rect x="270" y="7" width="125" height="2.4" fill="#2a2f45"/>
    </svg>
    <span class="web">www.terrakova.com</span>
  </div>
</section>

<!-- business card back -->
<section class="piece card-back" aria-label="Business card back">
  <div class="wordmark">terra kova</div>
</section>

<!-- envelope back, white flap -->
<section class="piece envelope-back white-flap" aria-label="Envelope back">
  <svg class="flap" width="395" height="50" viewBox="0 0 395 50"><path d="M0 0H395L384 37Q380 47 367 47H28Q15 47 11 37Z" fill="#fafafa"/></svg>
  <div class="wordmark">terra kova</div>
</section>

<!-- business card back, tone-on-tone -->
<section class="piece card-emboss" aria-label="Business card back, tone on tone">
  <div class="wordmark">terra kova</div>
</section>

<!-- envelope back, green flap -->
<section class="piece envelope-back green-flap" aria-label="Envelope back with green flap">
  <svg class="flap" width="395" height="50" viewBox="0 0 395 50"><path d="M0 0H395L384 37Q380 47 367 47H28Q15 47 11 37Z" fill="#36b677"/></svg>
  <div class="wordmark">terra kova</div>
</section>

<!-- letterhead -->
<section class="piece letter" aria-label="Letterhead">
  <header class="letter-head">
    <div class="wordmark">terra kova</div>
    <span class="divider"></span>
    <ul class="contact-list">
      <li><svg width="5" height="5" viewBox="0 0 10 10"><path d="M2 1l2 2-1 1.4c.6 1.2 1.4 2 2.6 2.6L7 6l2 2-1.4 1.5C4.5 9 1 5.5.5 2.4z" fill="#36b677"/></svg>555-014-2100</li>
      <li><svg width="5" height="5" viewBox="0 0 10 10"><rect x=".8" y="2" width="8.4" height="6" fill="#36b677"/></svg>info@terrakova.com</li>
    </ul>
    <span class="divider"></span>
    <p class="address">Your address, city<br>state, ZIP 0000</p>
  </header>
  <div class="letter-body">
    <p class="salutation">Dear Mr. Reyes,</p>
    <p>Lorem ipsum dolor sit amet, consectetuer adipiscing elit, sed diam nonmmy nibh euismod tincidunt ut laor eet dolore magna aliquam erat volutpat. Ut wisi enim ad minim veniam, quis nostrud exerci tationmcorper suscipit lobortis nisl ut aliquip ex ea commodo consequat. Duis autem vel eum iriure dolor in hendrerit in vulputate velit esse molestie consequat, vel illum dolore eu feugiat</p>
    <p>Rorem ipsum dolor sit amet, consectetuer adipiscing elit, sed diam nonmmy nibh euismod tincidunt ut laor eet dolore magna aliquam erat volutpat. Ut wisi enim ad minim veniam, quis nostrud exerci tationmcorper suscipit lobortis nisl ut aliquip ex ea commodo consequat. Duis autem vel eum iriure dolor in hendrerit in vulputate velit esse molest</p>
    <p>Dorem ipsum dolor sit amet, consectetuer adipiscing elit, sed diam nonmmy nibh euismod tincidunt ut laor eet dolore magna aliquam erat volutpat. Ut wisi enim ad minim veniam, quis nostrud exerci tationmcorper suscipit lobortis nisl ut aliquip ex ea commodo consequat. Duis autem vel eum iriure dolor in hendrerit in suscipit lobortis nisl ut aliquip ex ea commodo consequat. Duis autem vel eum iriure dolor in hendrerit in vulputate velit esse molestie consequat, vel illum</p>
    <p>Sorem ipsum dolor sit amet, consectetuer adipiscing elit, sed diam nonmmy nibh euismod tincidunt ut laor eet dolore magna aliquam erat volutpat. Ut wisi enim ad minim veniam, quis nostrud exerci tationmcorper suscipit lobortis nisl ut aliquip ex ea commodo consequat. Duis autem vel eum iriure dolor in</p>
    <p class="closing">Sincerely,</p>
    <div class="signature" role="img" aria-label="Handwritten signature"></div>
  </div>
  <div class="footer">
    <svg width="359" height="16" viewBox="0 0 359 16">
      <path d="M0 0H126Q131 0 135 5L139 11H359V16H0Z" fill="#36b677"/>
      <rect x="134" y="6.3" width="105" height="2.3" fill="#f07f2a"/>
      <rect x="242" y="6.3" width="117" height="2.3" fill="#2a2f45"/>
    </svg>
    <span class="web">www.terrakova.com</span>
  </div>
</section>

<!-- presentation folder, closed -->
<section class="piece folder-closed" aria-label="Presentation folder, cover and inside">
  <div class="folder-cover"><div class="wordmark">terra kova</div></div>
  <div class="folder-inside">
    <header class="mini-head">
      <div class="wordmark">terra kova</div>
      <span class="divider"></span>
      <p class="mini-text">555-014-2100<br>info@terrakova.com</p>
      <span class="divider"></span>
      <p class="mini-text">Your address, city<br>state, ZIP 0000</p>
    </header>
    <div class="footer">
      <svg width="171" height="8" viewBox="0 0 171 8">
        <path d="M0 0H58Q61 0 63 3L65 6H171V8H0Z" fill="#36b677"/>
        <rect x="64" y="3.3" width="52" height="1.2" fill="#f07f2a"/>
        <rect x="118" y="3.3" width="53" height="1.2" fill="#2a2f45"/>
      </svg>
      <span class="web">www.terrakova.com</span>
    </div>
  </div>
</section>

<!-- presentation folder, open -->
<section class="piece folder-open" aria-label="Presentation folder, open with letter">
  <div class="left-panel"></div>
  <div class="fold-gap"></div>
  <div class="mini-letter">
    <header class="mini-head">
      <div class="wordmark">terra kova</div>
      <span class="divider"></span>
      <p class="mini-text">555-014-2100<br>info@terrakova.com</p>
      <span class="divider"></span>
      <p class="mini-text">Your address, city<br>state, ZIP 0000</p>
    </header>
    <div class="mini-body">
      <p class="salutation">Dear Mr. Reyes,</p>
      <p>We are pleased to share our new studio plans with you. Our team has prepared a clear outline of the work, the schedule and the budget for your review this month.</p>
      <p>We are pleased to share our new studio plans with you. Our team has prepared a clear outline of the work, the schedule and the budget for your review this month.</p>
      <p>We are pleased to share our new studio plans with you. Our team has prepared a clear outline of the work, the schedule and the budget for your review this month.</p>
      <p>We are pleased to share our new studio plans with you. Our team has prepared a clear outline of the work, the schedule and the budget for your review this month.</p>
      <p class="closing">Sincerely,</p>
    </div>
  </div>
  <svg class="pockets" width="341" height="241" viewBox="0 0 341 241">
    <path d="M0 153H150Q157 153 158 160L170 241H0Z" fill="#1fc174"/>
    <path d="M341 153H191Q183 153 181 160L171 241H341Z" fill="#1fc174"/>
  </svg>
</section>

</body>
</html>
```